Quorbelline.io - Please redesign to make it look better from current design

We already have the current website, that you can access but we think it can improve from current version.
Quorbelline is a cryptocurrency hedge fund that allow you to participate in the hedge fund with cryptocurrency such as eth.
At current phase, we are doing an ICO, then we want to make sure that the website it looks professional, beautiful and trustable enough for investors after looking at our website.
Target Market(s)
Investors
Industry/Entity Type
Investment
Coding
Coded - Design and coding required
Number of Pages Required
1 page
Look and feel
Each slider illustrates characteristics of the customer's brand and the style your logo design should communicate.

```html
<!DOCTYPE html>
<html lang="en">
<head>
<meta charset="utf-8">
<title>Quorbelline.io</title>
<link href="https://fonts.googleapis.com/css2?family=Jost:wght@400;500;600;700&family=Mulish:wght@400;600;700&display=swap" rel="stylesheet">
<style>
:root{
  --blue:#0a52a3;
  --navy:#06408a;
  --sky:#1b8fd0;
  --ink:#444b55;
  --white:#ffffff;
  --line:#c9d8ea;
}
*{box-sizing:border-box;margin:0;padding:0}
html,body{width:1200px;height:2970px;overflow:hidden;background:var(--white)}
body{position:relative;font-family:"Mulish",sans-serif;color:var(--ink)}
.abs{position:absolute}
h1,h2,h3,h4,h5,.btn,.nav a,.brand{font-family:"Jost",sans-serif}

/* header */
.brand{position:absolute;display:flex;align-items:center;gap:12px;font-weight:600}
.brand .dot{width:44px;height:44px;border-radius:50%}
.header-brand{left:130px;top:40px;font-size:30px;color:var(--blue)}
.header-brand .dot{background:var(--blue)}
.call{left:748px;top:28px;display:flex;align-items:center;gap:10px}
.call .ring{width:36px;height:36px;border:2px solid var(--navy);border-radius:50%;display:flex;align-items:center;justify-content:center}
.call small{display:block;font-size:10px;color:var(--blue);letter-spacing:.5px}
.call strong{display:block;font-size:20px;color:var(--blue);font-family:"Jost",sans-serif;font-weight:600;line-height:1}
.search{left:964px;top:33px;width:104px;height:32px;border:1px solid #b8c2cc;font-size:9px;color:#556;display:flex;align-items:center;padding-left:8px;gap:5px;letter-spacing:.5px}
.nav{left:596px;top:89px;display:flex}
.nav a{display:block;font-size:12px;color:var(--blue);text-decoration:none;padding:6px 13px;margin-right:22px}
.nav a.active{background:var(--blue);color:var(--white)}

/* buttons */
.btn{display:flex;align-items:center;justify-content:center;background:var(--blue);color:var(--white);font-weight:500;letter-spacing:.5px}

/* hero */
.hero{left:0;top:130px;width:1200px;height:580px;background:linear-gradient(100deg,#3c5d80 0%,#7ea3c4 35%,#b9d4ea 55%,#5a86b3 80%,#2d5a8e 100%)}
.hero-title{left:740px;top:212px;color:var(--white);font-size:46px;line-height:48px;font-weight:600;letter-spacing:.5px}
.hero-btn{left:740px;top:333px;width:173px;height:54px;font-size:17px}
.dots{left:548px;top:640px;display:flex;gap:9px}
.dots i{width:9px;height:9px;border-radius:50%;border:1.5px solid var(--white)}
.dots i.on{background:var(--white)}

/* welcome */
.section-title{position:absolute;left:0;width:1200px;text-align:center;font-weight:600;font-size:27px;letter-spacing:.5px}
.welcome-title{top:765px;color:var(--blue)}
.lead{left:345px;top:828px;width:510px;text-align:center;font-size:13.5px;line-height:19px}
.welcome-btn{left:534px;top:946px;width:132px;height:40px;font-size:14px}

/* team */
.team{left:0;top:1050px;width:1200px;height:670px;background:var(--blue)}
.team-title{top:1112px;color:var(--white)}
.rule{left:569px;top:1163px;width:62px;height:3px;background:var(--white)}
.member{position:absolute;top:1235px;width:300px;text-align:center;color:var(--white)}
.member .photo{width:190px;height:190px;border-radius:50%;margin:0 auto 33px}
.member h3{font-size:15px;font-weight:600;letter-spacing:.3px}
.member h4{font-size:12px;font-weight:600;margin-top:1px}
.member p{font-size:12.5px;line-height:17px;width:210px;margin:16px auto 0;height:100px}
.member .btn{width:95px;height:30px;font-size:10px;background:var(--sky);margin:8px auto 0}

/* process */
.process-title{top:1778px;color:var(--blue)}
.subhead{position:absolute;left:0;width:1200px;text-align:center;color:var(--sky);font-size:15px;font-weight:500;letter-spacing:.3px}
.process-text{left:310px;top:1925px;width:580px;text-align:center;font-size:13.5px;line-height:20px}
.dist{position:absolute;top:2140px;width:240px}
.dist li{list-style:none;display:flex;gap:12px;font-size:12.5px;line-height:17px;margin-bottom:35px}
.dist li::before{content:"";flex:0 0 20px;height:12px;border-radius:6px;background:var(--sky);margin-top:3px}
.divider{top:2145px;width:2px;height:110px;background:var(--line)}

/* info band */
.info{left:0;top:2345px;width:1200px;height:355px;background:linear-gradient(110deg,#1c5fa8 0%,#3f86c7 45%,#6ba6d8 70%,#2b6db2 100%)}
.info-title{top:2440px;color:var(--white);font-size:39px;font-weight:600}
.info-btn{left:427px;top:2527px;width:344px;height:68px;font-size:18px;background:var(--navy);border:2px solid var(--white)}

/* footer */
.footer-bg{left:0;top:2700px;width:1200px;height:270px;background:var(--blue)}
.site-footer{color:var(--white)}
.footer-brand{left:130px;top:2810px;color:var(--white);font-size:28px}
.footer-brand .dot{background:var(--white)}
.fcol{position:absolute;top:2752px;font-size:11.5px;line-height:22px;color:var(--white)}
.fcol h5{font-size:12px;font-weight:600;letter-spacing:.5px;margin-bottom:12px}
.social{display:flex;gap:9px;margin-top:4px}
.social i{width:28px;height:28px;border-radius:50%;background:var(--sky)}
.social i:nth-child(3){background:#e4624e}
.social i:nth-child(4){background:#8e6bbd}
.fline{left:860px;top:2892px;width:206px;height:2px;background:var(--white)}
.copy{left:866px;top:2910px;font-size:11.5px;color:var(--white)}
</style>
</head>
<body>

<header class="site-header">
  <div class="brand header-brand"><span class="dot"></span>Quorbelline</div>
  <div class="abs call">
    <span class="ring"><svg width="16" height="16" viewBox="0 0 24 24"><path d="M6.6 10.8a15 15 0 0 0 6.6 6.6l2.2-2.2c.3-.3.7-.4 1-.2 1.1.4 2.3.6 3.6.6.6 0 1 .4 1 1V20c0 .6-.4 1-1 1A17 17 0 0 1 3 4c0-.6.4-1 1-1h3.5c.6 0 1 .4 1 1 0 1.3.2 2.5.6 3.6.1.3 0 .7-.2 1z" fill="#06408a"/></svg></span>
    <span><small>CALL US NOW</small><strong>555.010.2468</strong></span>
  </div>
  <div class="abs search"><svg width="9" height="9" viewBox="0 0 10 10"><circle cx="4" cy="4" r="3" fill="none" stroke="#445" stroke-width="1.3"/><path d="M6.3 6.3 9 9" stroke="#445" stroke-width="1.3"/></svg>SEARCH</div>
  <nav class="abs nav">
    <a class="active">HOME</a><a>ABOUT US</a><a>PROCESS</a><a>SERVICES</a><a>CONTACT US</a>
  </nav>
</header>

<section class="hero-wrap">
  <div class="abs hero" role="img" aria-label="Photo of a hand touching a rising chart of arrows and percentages"></div>
  <h1 class="abs hero-title">DIGITAL ASSET<br>MANAGEMENT</h1>
  <div class="abs btn hero-btn">READ MORE</div>
  <div class="abs dots"><i></i><i class="on"></i><i></i><i></i><i></i></div>
</section>

<section class="welcome">
  <h2 class="section-title welcome-title">WELCOME TO OUR SITE</h2>
  <p class="abs lead">Quorbelline process and manages on hedge fund strategy models which invests in a diversified portfolio of blockchain tokens. Blockchain tokens are emerging which add a monetary incentive layer to p2p protocols and facilitate equity crowdfunding that anyone in the world can participate in.</p>
  <div class="abs btn welcome-btn">READ MORE</div>
</section>

<section class="team-wrap">
  <div class="abs team"></div>
  <h2 class="section-title team-title">EXECUTIVE TEAM</h2>
  <div class="abs rule"></div>
  <div class="member" style="left:107px">
    <div class="photo" role="img" aria-label="Portrait of the director" style="background:radial-gradient(circle,#8a6f60,#3b3230)"></div>
    <h3>DOVRIN KELMARASET</h3><h4>DIRECTOR</h4>
    <p>As a hedge fund manager, Kelmaraset is the Chief Executive Officer of Brindlewood Capital LLC, an investment manager of Calloway Ridge Fund SP</p>
    <div class="btn">READ MORE</div>
  </div>
  <div class="member" style="left:450px">
    <div class="photo" role="img" aria-label="Portrait of the technical advisor" style="background:radial-gradient(circle,#c9b49a,#dfe6d2)"></div>
    <h3>TALVESH OMBRIN</h3><h4>TECHNICAL ADVISOR</h4>
    <p>Ombrin has various experienced on cryptocurrency and blockchain technology. He created what was the world's 4th most valuable cryptocurrency in February 2014</p>
    <div class="btn">READ MORE</div>
  </div>
  <div class="member" style="left:800px">
    <div class="photo" role="img" aria-label="Portrait of the marketing consultant" style="background:radial-gradient(circle,#c59a7c,#8a4a2a)"></div>
    <h3>SORAVIN PELTHANAKORN</h3><h4>MARKETING CONSULTANT</h4>
    <p>Pelthanakorn embeds a decade of experience in brand building, strategic planning, and marketing communication across the global agencies.</p>
    <div class="btn">READ MORE</div>
  </div>
</section>

<section class="process">
  <h2 class="section-title process-title">PROCESS</h2>
  <h3 class="subhead" style="top:1884px">HEDGE FUND MODEL</h3>
  <p class="abs process-text">Quorbelline run on closed-end fund （CEF）model which offers its shares to investors and utilize the fund to speculate and invest in the innovative blockchain tokens. Quorbelline will charge an upfront annual operation fee 4% of the money raised during the ICO. After that, the fund will charge a quarterly performance of 50% on the net profit made.</p>
  <h3 class="subhead" style="top:2074px">NET PROFIT DISTRIBUTION</h3>
  <ul class="dist" style="left:150px"><li>50 % of net profit is distributed to investors</li><li>0 – 5 % net profit &gt; 0% performance fee</li></ul>
  <div class="abs divider" style="left:434px"></div>
  <ul class="dist" style="left:500px"><li>5 – 10% net profit &gt; 5% performance fee</li><li>10-15 % net profit &gt; 13% performance fee</li></ul>
  <div class="abs divider" style="left:749px"></div>
  <ul class="dist" style="left:808px"><li>&gt; 15% net profit &gt; 15% performance fee</li><li>The remainder 50% minus performance fee, so at least 35%) is reinvested</li></ul>
</section>

<section class="info-wrap">
  <div class="abs info" role="img" aria-label="Photo of a person working with financial charts on a tablet, tinted blue"></div>
  <h2 class="section-title info-title">FOR MORE INFORMATION</h2>
  <div class="abs btn info-btn">DOWNLOAD WHITEPAPAER</div>
</section>

<footer class="site-footer">
  <div class="abs footer-bg"></div>
  <div class="brand footer-brand"><span class="dot"></span>Quorbelline</div>
  <div class="fcol" style="left:388px">
    <h5>CONTACT US</h5>
    Suite 12-18, 9B/F., East Wing,<br>Larkspur Trade Centre,<br>Marlowe Quay, 42,<br>Fenwick Road, Westhollow,<br>Port Averin.
  </div>
  <div class="fcol" style="left:688px">
    <h5>LINKS</h5>
    Home<br>About us<br>Services<br>Process<br>Contact us
  </div>
  <div class="fcol" style="left:863px">
    <h5>FOLLOW US ON</h5>
    <div class="social"><i></i><i></i><i></i><i></i></div>
  </div>
  <div class="abs fline"></div>
  <div class="abs copy">Copyrights @ 2017 All Rights Reserved</div>
</footer>

</body>
</html>
```